Roofing Contractor business card redesign

I want to redesign my business card with a fresh, eye catching concept

Target Market(s)

Residential Roofing Clients, potential employees, and subcontractors.

Industry/Entity Type

Business

Colors

Designer to choose colors to be used in the design.

Requirements
Nice to have
• I just want something that's more pleasing to the eye. You can use a combination of either / or of my logos.

```html
<!DOCTYPE html>
<html lang="en">
<head>
<meta charset="utf-8">
<title>Fair Hands Roofing Co. — Business Card</title>
<link rel="stylesheet" href="https://fonts.googleapis.com/css2?family=Oswald:wght@500&family=Work+Sans:wght@400;700&display=swap">
<style>
  :root {
    --bg: #2b2b2b;
    --card: #ffffff;
    --orange: #f58220;
    --brown: #45120e;
    --ink: #2a2a2a;
  }
  * { margin: 0; padding: 0; box-sizing: border-box; }
  html, body { width: 1200px; height: 930px; overflow: hidden; }
  body { background: var(--bg); position: relative; font-family: "Work Sans", sans-serif; }

  .card { position: absolute; left: 278px; width: 644px; height: 368px; border-radius: 22px; overflow: hidden; }

  .card--front { top: 76px; background: var(--card); }
  .brand-mark { position: absolute; left: 80px; top: 94px; width: 150px; display: flex; flex-direction: column; align-items: center; gap: 10px; }
  .brand-mark__circle { width: 104px; height: 104px; border-radius: 50%; background: var(--orange); }
  .brand-mark__name { font-weight: 700; font-size: 21px; color: var(--brown); text-align: center; line-height: 1.1; }

  .divider { position: absolute; left: 299px; top: 94px; width: 2px; height: 176px; background: var(--orange); }

  .contact { position: absolute; left: 350px; top: 90px; color: var(--ink); font-weight: 400; font-size: 15px; line-height: 19px; }
  .contact__name { font-family: "Oswald", sans-serif; font-weight: 500; font-size: 31px; line-height: 36px; color: var(--orange); letter-spacing: 1px; text-transform: uppercase; margin-bottom: 2px; }
  .contact__address { margin-top: 7px; font-size: 16px; line-height: 21px; }
  .contact__lines { margin-top: 7px; list-style: none; font-size: 16px; line-height: 20px; }
  .contact__lines li { display: flex; align-items: center; gap: 12px; }
  .contact__lines svg { width: 11px; height: 11px; flex: none; }

  .stripe { position: absolute; left: 0; right: 0; bottom: 0; height: 18px; display: flex; gap: 4px; background: var(--card); }
  .stripe__end { width: 80px; background: var(--orange); }
  .stripe__mid { flex: 1; background: var(--brown); }

  .card--back { top: 486px; background: var(--brown); display: flex; flex-direction: column; align-items: center; justify-content: center; color: #fff; font-weight: 700; }
  .back-name { display: flex; align-items: center; gap: 14px; font-size: 62px; line-height: 1; }
  .back-name__circle { width: 92px; height: 92px; border-radius: 50%; background: #fff; }
  .back-tagline { margin-top: 14px; font-size: 32px; line-height: 1; }
</style>
</head>
<body>
  <section class="card card--front" aria-label="Card front">
    <div class="brand-mark">
      <div class="brand-mark__circle"></div>
      <div class="brand-mark__name">Fair Hands<br>Roofing Co.</div>
    </div>
    <div class="divider"></div>
    <div class="contact">
      <h1 class="contact__name">Dan Whitaker</h1>
      <p>Ridgeline Certified Roof Inspector<br>Licensed Property Adjuster</p>
      <p class="contact__address">4810 Cedar Ridge Lane<br>Suite 118 Plano, TX 75093</p>
      <ul class="contact__lines">
        <li><svg viewBox="0 0 12 12"><path d="M2.5 1 L4.5 1 L5 3.5 L3.8 4.5 Q5 7.2 7.5 8.2 L8.5 7 L11 7.5 L11 9.5 Q10.5 11 9 11 Q1 10 1 2.5 Q1 1 2.5 1Z" fill="none" stroke="#f58220" stroke-width="1.2"/></svg>(555) 014-2000</li>
        <li><svg viewBox="0 0 12 12"><rect x="3" y="0.8" width="6" height="10.4" rx="1.2" fill="none" stroke="#f58220" stroke-width="1.3"/><circle cx="6" cy="9.2" r="0.7" fill="#f58220"/></svg>(555) 018-7731</li>
        <li><svg viewBox="0 0 12 12"><rect x="0.8" y="2.5" width="10.4" height="7" fill="none" stroke="#f58220" stroke-width="1.2"/><path d="M1 3 L6 6.6 L11 3" fill="none" stroke="#f58220" stroke-width="1.2"/></svg>dan@fairhandsroofing.com</li>
      </ul>
    </div>
    <div class="stripe"><div class="stripe__end"></div><div class="stripe__mid"></div><div class="stripe__end"></div></div>
  </section>

  <section class="card card--back" aria-label="Card back">
    <div class="back-name"><span>Fair</span><span class="back-name__circle"></span><span>Hands</span></div>
    <div class="back-tagline">Roofing Co.</div>
  </section>
</body>
</html>
```